Chimney Service company needs new business card design

We need a updated business card with our new logo added. We provide a full range of chimney services throughout Vermont and New Hampshire. The business card will be one sided and color. Attached is our current business card another document showing all the information we would like on the card.
We dont like a lot of flashy colors.... here is a link to our website to get an idea of our branding www.flueguardianvt.example

Target Market(s)

homeowners

Industry/Entity Type

Business

Contact Information for Business Card

See attached sheet for content.

Font styles to use
Serif
Sans Serif

Requirements
Must have
• all information provided on separate sheet
Should not have
• Additional information that may clogg up design

```html
<!DOCTYPE html>
<html lang="en">
<head>
<meta charset="utf-8">
<title>Flue Guardian – Business Card</title>
<link href="https://fonts.googleapis.com/css2?family=Cinzel:wght@400;500&family=Lato:wght@400&display=swap" rel="stylesheet">
<style>
  :root {
    --backdrop: #4b4b4b;
    --card-dark: #3a3a3a;
    --card-red: #930000;
    --accent-red: #b3121b;
    --text-light: #f2f2f2;
    --text-soft: #d9d9d9;
    --rule: #5e5e5e;
  }
  * { margin: 0; padding: 0; box-sizing: border-box; }
  html, body { width: 1200px; height: 900px; overflow: hidden; }
  body { background: var(--backdrop); position: relative; font-family: "Lato", Arial, sans-serif; }

  .card {
    position: absolute;
    top: 306px;
    width: 438px;
    height: 272px;
    border-radius: 11px;
  }
  .card--front { left: 150px; background: var(--card-dark); color: var(--text-light); }
  .card--back { left: 610px; background: var(--card-red); color: #fff; }

  .brand { position: absolute; display: flex; align-items: center; font-family: "Cinzel", Georgia, serif; font-weight: 500; color: #fff; letter-spacing: 0.5px; }
  .brand__mark { border: 4px solid #fff; }
  .card--front .brand { right: 26px; top: 46px; gap: 10px; font-size: 23px; }
  .card--front .brand__mark { width: 46px; height: 46px; border-width: 3px; }

  .card--back .brand { left: 0; right: 0; top: 69px; flex-direction: column; gap: 20px; font-size: 27px; }
  .card--back .brand__mark { width: 89px; height: 89px; }

  .tagline {
    position: absolute; right: 22px; top: 113px;
    font-family: "Cinzel", Georgia, serif; font-size: 14px; color: var(--text-soft); letter-spacing: 0.4px;
  }
  .divider { position: absolute; left: 22px; right: 22px; top: 160px; height: 1px; background: var(--rule); }

  .services { position: absolute; left: 24px; top: 168px; list-style: none; font-size: 12.5px; line-height: 16px; color: var(--text-soft); }
  .services li { display: flex; align-items: center; gap: 5px; }
  .services li::before { content: ""; width: 6px; height: 6px; background: var(--accent-red); }

  .contacts { position: absolute; right: 20px; top: 199px; list-style: none; font-size: 12.5px; line-height: 16px; color: var(--text-light); text-align: right; }
  .contacts li { display: flex; justify-content: flex-end; align-items: center; gap: 4px; }
  .contacts svg { width: 10px; height: 10px; fill: none; stroke: var(--accent-red); stroke-width: 1.6; }
</style>
</head>
<body>
  <section class="card card--front">
    <div class="brand"><span class="brand__mark"></span><span class="brand__name">FLUE GUARDIAN</span></div>
    <p class="tagline">Serving VT and New Hampshire since 1989</p>
    <div class="divider"></div>
    <ul class="services">
      <li>Full Masonry Services</li>
      <li>Historic chimney restoration</li>
      <li>Stainless steel liners</li>
      <li>New Chimney installations</li>
      <li>HSCA Certified Chimney sweeps</li>
    </ul>
    <ul class="contacts">
      <li>802-555-0147
        <svg viewBox="0 0 10 10" aria-hidden="true"><path d="M2 1 L4 3 L3 4.5 Q4.5 6.5 5.5 7 L7 6 L9 8 L7.5 9.5 Q3 8.5 0.5 2.5 Z"/></svg>
      </li>
      <li>info@flueguardianvt.example
        <svg viewBox="0 0 10 10" aria-hidden="true"><rect x="1" y="2" width="8" height="6"/><path d="M1 2 L5 5.5 L9 2"/></svg>
      </li>
      <li>www.flueguardianvt.example
        <svg viewBox="0 0 10 10" aria-hidden="true"><circle cx="5" cy="5" r="4"/><path d="M1 5 H9 M5 1 Q2.5 5 5 9 Q7.5 5 5 1"/></svg>
      </li>
    </ul>
  </section>

  <section class="card card--back">
    <div class="brand"><span class="brand__mark"></span><span class="brand__name">FLUE GUARDIAN</span></div>
  </section>
</body>
</html>
```